Talvex Health Artificial Intelligence MedTech Software Website Refresh

We need a new website (old one at www.talvex-health.example is no longer relevant) for our medtech software company using artificial intelligence to deliver higher quality, faster and more cost effective care in oncology. The audiences are both healthcare providers and health insurance payers. We've created an extensive outline to follow and have the old site still live for easy content use and repurposing. Our primary need is a great overhaul to look and feel. If we find a successful designer, we will need additional work done for graphics and other presentation projects.

Target Market(s)

Health care providers (doctors) and administrators plus health insurers

Industry/Entity Type

Medtech

Coding

Number of Pages Required

5+ page

Font styles to use
Other font styles liked:
• Roboto see Style Guide

Requirements
Must have
• See attached brief
Nice to have
• See attached brief. We like www.caremint.example and www.lumoradx.example as sites.
Should not have
• See attached brief

```html
<!DOCTYPE html>
<html lang="en">
<head>
<meta charset="utf-8">
<title>Talvex Health – Website Concepts</title>
<link rel="stylesheet" href="https://fonts.googleapis.com/css2?family=Roboto:wght@300;400;500;700;900&display=swap">
<style>
:root{
  --board:#c9c9c9;
  --blue:#1b7fd6;
  --blue-dark:#1565c0;
  --blue-bright:#2a9ae6;
  --navy:#0f2b55;
  --ink:#1d2733;
  --text:#555b63;
  --muted:#9aa1a9;
  --line:#e1e4e8;
  --grey-band:#f0f0f0;
  --white:#ffffff;
}
*{margin:0;padding:0;box-sizing:border-box}
html,body{width:737px;height:1200px;overflow:hidden}
body{background:var(--board);font-family:'Roboto',sans-serif;color:var(--ink);position:relative}
.page{position:absolute;width:613px;background:var(--white);transform:scale(.4874);transform-origin:0 0;overflow:hidden;box-shadow:0 2px 8px rgba(0,0,0,.12)}
.page--full{left:49px;top:43px;height:2267px}
.page--compact{left:389px;top:43px;height:1836px}
.section{position:absolute;left:0;width:613px}
.abs{position:absolute}

/* hero */
.hero{top:0;height:333px;background:linear-gradient(160deg,#1f86dc 0%,#1a78d0 60%,#1870c8 100%)}
.brand{position:absolute;left:57px;top:26px;color:var(--white);font-weight:700;font-size:24px;letter-spacing:.2px}
.brand::after{content:"";display:inline-block;width:8px;height:8px;background:#8fd0ff;margin-left:5px;vertical-align:middle}
.nav{position:absolute;right:57px;top:38px;display:flex;gap:13px;font-size:7.4px;font-weight:500;color:var(--white)}
.nav .is-active{color:#8cc7f5;border-bottom:1px solid #8cc7f5;padding-bottom:3px}
.hero-title{position:absolute;left:57px;top:128px;font-size:26px;font-weight:900;color:var(--white);letter-spacing:.3px}
.hero-lead{position:absolute;left:57px;top:166px;width:262px;font-size:8.3px;line-height:14px;color:var(--white)}
.pill{position:absolute;height:23px;border-radius:12px;background:var(--blue-bright);color:var(--white);font-size:7.5px;font-weight:700;display:flex;align-items:center;justify-content:center}
.hero .pill{left:57px;top:222px;width:89px}
.bubble{position:absolute;width:104px;height:104px;border-radius:50%;background:var(--white);color:var(--blue-dark);font-size:8.6px;font-weight:700;line-height:12px;display:flex;align-items:center;justify-content:center;text-align:center;padding:0 14px}
.bubble--providers{left:450px;top:60px}
.bubble--payers{left:317px;top:193px}
.phone{position:absolute;left:405px;top:140px;width:120px;height:243px;border:5px solid #1b1b1b;border-radius:18px;background:linear-gradient(170deg,#3aa7ee,#1d86d8);box-shadow:0 8px 14px rgba(0,0,0,.25);z-index:2}
.phone::before{content:"";position:absolute;left:32px;top:0;width:46px;height:8px;background:#1b1b1b;border-radius:0 0 6px 6px}
.phone-name{position:absolute;left:0;right:0;top:98px;text-align:center;color:var(--white);font-weight:700;font-size:13px}

/* solutions */
.solutions{top:333px;height:320px}
.section-title{position:absolute;left:0;right:0;text-align:center;font-size:18px;font-weight:500;color:var(--ink)}
.section-title em{font-style:normal;color:var(--blue-dark)}
.solutions .section-title{top:88px}
.benefit{position:absolute;top:132px;width:124px;text-align:center}
.benefit-icon{width:52px;height:52px;border-radius:50%;background:#eef1f5;margin:0 auto;display:flex;align-items:center;justify-content:center}
.benefit h3{margin-top:10px;font-size:8.6px;font-weight:700;color:var(--ink)}
.benefit p{margin-top:6px;font-size:6.8px;line-height:11px;color:var(--text)}
.demo{left:258px;width:97px;top:272px}

/* feature rows */
.feature{height:207px}
.photo{position:absolute;top:0;width:306px;height:207px}
.feature-body{position:absolute;width:250px}
.feature-title{font-size:17px;font-weight:700;color:var(--ink)}
.feature-title em{font-style:normal;color:var(--blue-dark)}
.product{display:flex;align-items:center;gap:6px;margin-top:12px;font-size:11px;font-weight:300;color:var(--blue-dark)}
.product i{width:10px;height:10px;background:#f2a32a;display:block}
.ticks{list-style:none;margin-top:12px}
.ticks li{position:relative;padding-left:14px;font-size:6.9px;line-height:11.6px;color:var(--text);margin-bottom:4px}
.ticks svg{position:absolute;left:0;top:2px;width:7px;height:7px}
.btn-small{display:flex;align-items:center;justify-content:center;width:70px;height:19px;border-radius:10px;background:var(--blue-dark);color:var(--white);font-size:6.6px;font-weight:700;margin-top:14px}

/* evidence */
.evidence{height:240px}
.evidence .section-title{top:8px}
.card{position:absolute;top:46px;width:159px;height:185px;border:1px solid var(--line);background:var(--white)}
.card-photo{height:105px}
.card h4{margin:11px 11px 0;font-size:8.3px;line-height:11px;font-weight:700;color:var(--ink)}
.card-meta{position:absolute;left:11px;top:139px;display:flex;gap:6px;align-items:center;font-size:6.2px;color:var(--muted)}
.card-meta svg{width:6px;height:6px}
.card-link{position:absolute;left:11px;top:164px;display:flex;gap:4px;align-items:center;font-size:6.8px;font-weight:500;color:var(--blue-dark)}
.card-link svg{width:7px;height:8px}

/* partners */
.partners{height:211px;background:var(--grey-band)}
.partners .section-title{top:28px;font-size:19px}
.partner-grid{position:absolute;left:57px;top:68px;width:498px;display:grid;grid-template-columns:repeat(4,1fr);grid-template-rows:52px 60px}
.partner{display:flex;align-items:center;justify-content:center;gap:5px;font-size:10px;font-weight:700;text-align:center;border-left:1px solid #dcdcdc}
.partner:nth-child(4n+1){border-left:0}
.partner i{width:14px;height:14px;border-radius:50%;display:block}

/* contact */
.contact{height:163px;background:var(--blue-dark);color:var(--white)}
.contact .section-title{top:22px;color:var(--white);font-size:20px}
.contact-item{position:absolute;top:66px;width:134px;text-align:center}
.contact-icon{width:24px;height:24px;border-radius:50%;background:var(--blue-bright);margin:0 auto;display:flex;align-items:center;justify-content:center}
.contact-icon svg{width:11px;height:11px}
.contact-item h5{margin-top:7px;font-size:7.4px;font-weight:700}
.contact-item p{margin-top:4px;font-size:6.8px;line-height:10.5px}

/* footer */
.footer{height:184px;background:var(--white)}
.footer-brand{position:absolute;left:57px;top:40px;font-size:22px;font-weight:700;color:var(--blue-dark)}
.social{position:absolute;left:63px;top:104px;display:flex;gap:4px}
.social i{width:18px;height:18px;border-radius:50%;border:1px solid #8a9099;display:block}
.foot-col{position:absolute;top:34px}
.foot-col h6{font-size:7.8px;font-weight:700;color:var(--ink);margin-bottom:8px}
.foot-col a{display:block;font-size:6.6px;color:var(--text);line-height:13.5px;text-decoration:none}
.office-row{position:relative;padding-left:12px;margin-bottom:6px;font-size:6.4px;line-height:9px;color:var(--text)}
.office-row b{display:block;color:var(--ink);font-size:6px}
.office-row svg{position:absolute;left:0;top:1px;width:7px;height:7px}
.footer-rule{position:absolute;left:57px;top:152px;width:499px;height:1px;background:var(--line)}
.copyright{position:absolute;left:0;right:0;top:161px;text-align:center;font-size:6.4px;color:var(--text)}

/* platform diagram */
.laptop-lid{position:absolute;left:111px;top:615px;width:391px;height:245px;background:#eff1f4;border:1px solid #dfe2e7;border-radius:8px 8px 0 0}
.laptop-screen{position:absolute;left:17px;top:17px;width:356px;height:220px;background:linear-gradient(160deg,#6a8aac,#56789c)}
.laptop-base{position:absolute;left:66px;top:860px;width:481px;height:14px;background:linear-gradient(#f3f4f6,#d9dce1);border-radius:0 0 50% 50%/0 0 100% 100%;box-shadow:0 10px 14px rgba(0,0,0,.12)}
.node{position:absolute;width:92px;height:92px;border-radius:50%;color:var(--white);text-align:center;display:flex;flex-direction:column;align-items:center;justify-content:center}
.node svg{width:18px;height:18px;margin-bottom:5px}
.node b{font-size:9px}
.node span{font-size:6.8px;line-height:10px;margin-top:2px}
.node--patient{left:260px;top:634px;background:#1b8ae0}
.node--payer{left:147px;top:751px;background:var(--navy)}
.node--core{left:260px;top:751px;background:var(--white);color:var(--blue-dark)}
.node--provider{left:371px;top:751px;background:#1b60b8}
</style>
</head>
<body>

<svg width="0" height="0" style="position:absolute" aria-hidden="true">
  <defs>
    <symbol id="tick" viewBox="0 0 10 10"><circle cx="5" cy="5" r="5" fill="#1b7fd6"/><path d="M2.6 5.2l1.6 1.6 3.2-3.4" fill="none" stroke="#fff" stroke-width="1.3"/></symbol>
    <symbol id="pin" viewBox="0 0 12 12"><path d="M6 1a3.6 3.6 0 0 0-3.6 3.6C2.4 7.3 6 11 6 11s3.6-3.7 3.6-6.4A3.6 3.6 0 0 0 6 1z" fill="#fff"/><circle cx="6" cy="4.6" r="1.3" fill="#2a9ae6"/></symbol>
    <symbol id="phone" viewBox="0 0 12 12"><path d="M3 1.2l1.8-.2 1 2.6-1.2.9a6.5 6.5 0 0 0 2.9 2.9l.9-1.2 2.6 1-.2 1.8c-.1.6-.6 1-1.2 1C5 10 2 7 2 2.4c0-.6.4-1.1 1-1.2z" fill="#fff"/></symbol>
    <symbol id="mail" viewBox="0 0 12 12"><rect x="1" y="2.5" width="10" height="7" rx="1" fill="#fff"/><path d="M1.5 3.2L6 6.5l4.5-3.3" fill="none" stroke="#2a9ae6" stroke-width=".9"/></symbol>
    <symbol id="cal" viewBox="0 0 10 10"><rect x="1" y="2" width="8" height="7" rx="1" fill="none" stroke="#9aa1a9"/><path d="M1 4h8" stroke="#9aa1a9"/></symbol>
    <symbol id="user" viewBox="0 0 10 10"><circle cx="5" cy="3" r="2" fill="#9aa1a9"/><path d="M1.5 9.5a3.5 3.5 0 0 1 7 0z" fill="#9aa1a9"/></symbol>
    <symbol id="doc" viewBox="0 0 10 12"><path d="M1.5 1h4.5l2.5 2.5V11h-7z" fill="none" stroke="#1565c0"/><path d="M3 6h4M3 8h4" stroke="#1565c0"/></symbol>
    <symbol id="ico-grid" viewBox="0 0 30 30"><g fill="none" stroke="#1565c0" stroke-width="1.2"><rect x="4" y="4" width="8" height="8"/><rect x="18" y="4" width="8" height="8"/><rect x="4" y="18" width="8" height="8"/><rect x="18" y="18" width="8" height="8"/><path d="M12 8h6M8 12v6M22 12v6M12 22h6"/></g></symbol>
    <symbol id="ico-gear" viewBox="0 0 30 30"><g fill="none" stroke="#1565c0" stroke-width="1.2"><circle cx="15" cy="15" r="9"/><circle cx="15" cy="15" r="3.5"/><path d="M15 3v4M15 23v4M3 15h4M23 15h4"/></g></symbol>
    <symbol id="ico-screen" viewBox="0 0 30 30"><g fill="none" stroke="#1565c0" stroke-width="1.2"><rect x="4" y="6" width="22" height="15" rx="1"/><path d="M11 25h8M15 21v4M12 13.5h6M15 10.5v6"/></g></symbol>
    <symbol id="ico-chart" viewBox="0 0 30 30"><g fill="none" stroke="#1565c0" stroke-width="1.2"><rect x="5" y="4" width="20" height="22" rx="1"/><path d="M9 21v-4M13 21v-7M17 21v-5M21 21v-9M9 9h8"/></g></symbol>
    <symbol id="ico-person" viewBox="0 0 20 20"><g fill="none" stroke="#fff" stroke-width="1.2"><circle cx="10" cy="6" r="3.5"/><path d="M3 18a7 7 0 0 1 14 0"/></g></symbol>
  </defs>
</svg>

<!-- ================= FULL PAGE ================= -->
<main class="page page--full">

  <header class="section hero">
    <div class="brand">Talvex Health</div>
    <nav class="nav"><span class="is-active">Home</span><span>Solutions</span><span>Clinical Evidence</span><span>About</span><span>Contact Us</span></nav>
    <h1 class="hero-title">TALVEX HEALTH</h1>
    <p class="hero-lead">Talvex Health, Inc. is an expert team with the vision of improving oncology treatment delivery, patient outcomes and cost effectiveness through the power of AI.</p>
    <span class="pill">REQUEST INFO</span>
    <div class="bubble bubble--providers">The problem(s) for providers</div>
    <div class="bubble bubble--payers">The problem for payers</div>
  </header>
  <div class="phone"><div class="phone-name">Talvex</div></div>

  <section class="section solutions">
    <h2 class="section-title">TALVEX HEALTH <em>HAS SOLUTIONS</em></h2>
    <div class="benefit" style="left:39px"><div class="benefit-icon"><svg width="30" height="30"><use href="#ico-grid"/></svg></div><h3>Integrated</h3><p>Integrated into MD clinical workflows and IT systems</p></div>
    <div class="benefit" style="left:173px"><div class="benefit-icon"><svg width="30" height="30"><use href="#ico-gear"/></svg></div><h3>Automated PA</h3><p>Automated PA removing manual processes, saving administrative costs</p></div>
    <div class="benefit" style="left:307px"><div class="benefit-icon"><svg width="30" height="30"><use href="#ico-screen"/></svg></div><h3>Improved care quality</h3><p>Improved care quality equal or better personalized care</p></div>
    <div class="benefit" style="left:440px"><div class="benefit-icon"><svg width="30" height="30"><use href="#ico-chart"/></svg></div><h3>Financial gains</h3><p>Financial gains through reduced write-offs and right-sized care</p></div>
    <span class="pill demo">Request A Demo</span>
  </section>

  <section class="section feature" style="top:691px">
    <div class="photo" style="left:0;background:linear-gradient(120deg,#dfe4ea,#bfc9d4 60%,#8fa2b8)" role="img" aria-label="Physician in a white coat reviewing a tablet with a nurse in a clinic"></div>
    <div class="feature-body" style="left:336px;top:16px">
      <h2 class="feature-title"><em>PAYER</em> SOLUTION</h2>
      <div class="product"><i></i>OncoView</div>
      <ul class="ticks">
        <li><svg><use href="#tick"/></svg>OpEx savings - removing unnecessary handoffs and manual processes</li>
        <li><svg><use href="#tick"/></svg>MedEx savings - helping to right size care (without compromising quality)</li>
        <li><svg><use href="#tick"/></svg>Provider engagement and satisfaction - credible and integrated solution in use by physician key opinion leaders</li>
        <li><svg><use href="#tick"/></svg>Case Study [placeholder]</li>
      </ul>
      <span class="btn-small">LEARN MORE</span>
    </div>
  </section>

  <section class="section feature" style="top:925px">
    <div class="feature-body" style="left:56px;top:18px">
      <h2 class="feature-title"><em>PROVIDER</em> SOLUTION</h2>
      <div class="product"><i></i>SwiftPair</div>
      <ul class="ticks">
        <li><svg><use href="#tick"/></svg>Physicians can achieve best quality on the first pass - evaluate tradeoffs inseconds and set a single resolved directive. Personalized medicine.</li>
        <li><svg><use href="#tick"/></svg>OpEx savings / efficiency - remove the repeated cycles of planning trial and error</li>
        <li><svg><use href="#tick"/></svg>Connected to prior authorization decisions - layer PA automation to find the best value while maintaining high quality care</li>
      </ul>
      <span class="btn-small">LEARN MORE</span>
    </div>
    <div class="photo" style="left:307px;background:linear-gradient(135deg,#0a2f7a,#1e63c8 45%,#0b1f55)" role="img" aria-label="Brain scan images on a light panel with a pen pointing at them"></div>
  </section>

  <section class="section feature" style="top:1159px">
    <div class="photo" style="left:0;background:linear-gradient(120deg,#2c3a4c,#3d6fb5 50%,#e19a4a)" role="img" aria-label="Patient monitor in an operating room with surgeons in blue gowns"></div>
    <div class="feature-body" style="left:336px;top:31px">
      <h2 class="feature-title">INNOVATION</h2>
      <ul class="ticks">
        <li><svg><use href="#tick"/></svg>Talvex Insight Artificial Intelligence (AI) decision support platform Clinically validated, FDA-cleared expert system with 30,000 patient treatmentdatasets</li>
        <li><svg><use href="#tick"/></svg>AI decodes patient complexity to provide visibility to best practice.</li>
        <li><svg><use href="#tick"/></svg>To meet the payer's need to make prior authorization (PA) decisions</li>
        <li><svg><use href="#tick"/></svg>To meet the provider's need for expert decision making</li>
      </ul>
      <span class="btn-small">LEARN MORE</span>
    </div>
  </section>

  <section class="section evidence" style="top:1415px">
    <h2 class="section-title">CLINICAL <em>EVIDENCE</em></h2>
    <article class="card" style="left:57px"><div class="card-photo" style="background:linear-gradient(135deg,#1b5fa8,#5aa7e0)" role="img" aria-label="Clinician holding a phone with an AI heart graphic"></div><h4>AI power saves time and improves treatment plan quality</h4><div class="card-meta"><svg><use href="#cal"/></svg>Dec 10, 2020 &nbsp;|&nbsp; <svg><use href="#user"/></svg>Alex Reed</div><div class="card-link"><svg><use href="#doc"/></svg>DownLoad Now</div></article>
    <article class="card" style="left:227px"><div class="card-photo" style="background:linear-gradient(135deg,#9fb4c8,#e4e9ef 50%,#2d4f8a)" role="img" aria-label="Doctor reviewing a folder beside digital health screens"></div><h4>Leveraging Artificial Intelligence (AI) clinical decision support</h4><div class="card-meta"><svg><use href="#cal"/></svg>Dec 10, 2020 &nbsp;|&nbsp; <svg><use href="#user"/></svg>Alex Reed</div><div class="card-link"><svg><use href="#doc"/></svg>DownLoad Now</div></article>
    <article class="card" style="left:396px"><div class="card-photo" style="background:linear-gradient(135deg,#6fa7c9,#2f77a8 60%,#cfe2ee)" role="img" aria-label="Surgeons working in a bright operating room"></div><h4>Implementation and impact of AI decision support software</h4><div class="card-meta"><svg><use href="#cal"/></svg>Dec 10, 2020 &nbsp;|&nbsp; <svg><use href="#user"/></svg>Alex Reed</div><div class="card-link"><svg><use href="#doc"/></svg>DownLoad Now</div></article>
  </section>

  <section class="section partners" style="top:1709px">
    <h2 class="section-title">Our <em>Partners</em></h2>
    <div class="partner-grid">
      <div class="partner" style="color:#4e2a84">Northgate Health</div>
      <div class="partner" style="color:#b0123b">Riverbend Health</div>
      <div class="partner" style="color:#1d3c6e">Bayline Clinic</div>
      <div class="partner" style="color:#0a5fb4">Southmere Cancer Center</div>
      <div class="partner" style="color:#5b6670">Lakeshore Health</div>
      <div class="partner" style="color:#1f3d7a"><i style="background:#f28c28"></i>Harborview Cancer Institute</div>
      <div class="partner" style="color:#1e6e82">Eastfield General</div>
      <div class="partner" style="color:#1e3a6e">Kingsley Women's Hospital</div>
    </div>
  </section>

  <section class="section contact" style="top:1920px">
    <h2 class="section-title">Contact Us</h2>
    <div class="contact-item" style="left:40px"><div class="contact-icon"><svg><use href="#pin"/></svg></div><h5>California Address</h5><p>480 Harbor Loop, Suite<br>12 Millbrae, CA 94030</p></div>
    <div class="contact-item" style="left:174px"><div class="contact-icon"><svg><use href="#pin"/></svg></div><h5>Boston Address</h5><p>18 Elm Wharf Second Floor<br>Salem Bay, MA 01970</p></div>
    <div class="contact-item" style="left:307px"><div class="contact-icon"><svg><use href="#phone"/></svg></div><h5>Phone</h5><p>(555) 014-2290</p></div>
    <div class="contact-item" style="left:440px"><div class="contact-icon"><svg><use href="#mail"/></svg></div><h5>Email</h5><p>info@talvex-health.example<br>support@talvex-health.example</p></div>
  </section>

  <footer class="section footer" style="top:2083px">
    <div class="footer-brand">Talvex Health</div>
    <div class="social"><i></i><i></i><i></i><i></i></div>
    <div class="foot-col" style="left:212px">
      <h6>Our Office Address</h6>
      <div class="office-row"><svg><use href="#phone"/></svg><b>Phone</b>(555) 014-2290</div>
      <div class="office-row"><svg><use href="#mail"/></svg><b>Email</b>info@talvex-health.example</div>
      <div class="office-row"><svg><use href="#pin"/></svg><b>Location</b>480 Harbor Loop Suite 12<br>Millbrae, CA 94030</div>
    </div>
    <div class="foot-col" style="left:386px"><h6>Company</h6><a>Home</a><a>Solutions</a><a>Clinical Evidence</a><a>About</a><a>Contact Us</a></div>
    <div class="foot-col" style="left:493px"><h6>Information</h6><a>Terms &amp; Conditions</a><a>Privacy Policy</a><a>Disclaimer</a><a>Site Map</a><a>Customer Support</a></div>
    <div class="footer-rule"></div>
    <p class="copyright">Copyrights ©talvex-health 2020 | Allrights Reserved</p>
  </footer>
</main>

<!-- ================= COMPACT PAGE ================= -->
<main class="page page--compact">

  <header class="section hero">
    <div class="brand">Talvex Health</div>
    <nav class="nav"><span class="is-active">Home</span><span>Solutions</span><span>Clinical Evidence</span><span>About</span><span>Contact Us</span></nav>
    <h1 class="hero-title">TALVEX HEALTH</h1>
    <p class="hero-lead">Talvex Health, Inc. is an expert team with the vision of improving oncology treatment delivery, patient outcomes and cost effectiveness through the power of AI.</p>
    <span class="pill">REQUEST INFO</span>
    <div class="bubble bubble--providers">The problem(s) for providers</div>
    <div class="bubble bubble--payers">The problem for payers</div>
  </header>
  <div class="phone"><div class="phone-name">Talvex</div></div>

  <section class="section solutions">
    <h2 class="section-title">TALVEX HEALTH <em>HAS SOLUTIONS</em></h2>
    <div class="benefit" style="left:39px"><div class="benefit-icon"><svg width="30" height="30"><use href="#ico-grid"/></svg></div><h3>Integrated</h3><p>Integrated into MD clinical workflows and IT systems</p></div>
    <div class="benefit" style="left:173px"><div class="benefit-icon"><svg width="30" height="30"><use href="#ico-gear"/></svg></div><h3>Automated PA</h3><p>Automated PA removing manual processes, saving administrative costs</p></div>
    <div class="benefit" style="left:307px"><div class="benefit-icon"><svg width="30" height="30"><use href="#ico-screen"/></svg></div><h3>Improved care quality</h3><p>Improved care quality equal or better personalized care</p></div>
    <div class="benefit" style="left:440px"><div class="benefit-icon"><svg width="30" height="30"><use href="#ico-chart"/></svg></div><h3>Financial gains</h3><p>Financial gains through reduced write-offs and right-sized care</p></div>
  </section>

  <div class="laptop-lid"><div class="laptop-screen"></div></div>
  <div class="laptop-base"></div>
  <div class="node node--patient"><svg><use href="#ico-person"/></svg><b>Patient</b><span>30% reduction in side<br>effects</span></div>
  <div class="node node--payer"><svg><use href="#ico-person"/></svg><b>Payer</b><span>$15M PMPY</span></div>
  <div class="node node--core"><b style="font-size:12px">Talvex</b></div>
  <div class="node node--provider"><svg><use href="#ico-person"/></svg><b>Provider</b><span>$4K/Patient</span></div>
  <span class="pill" style="left:258px;width:97px;top:929px">Request A Demo</span>

  <section class="section evidence" style="top:986px">
    <h2 class="section-title">CLINICAL <em>EVIDENCE</em></h2>
    <article class="card" style="left:57px"><div class="card-photo" style="background:linear-gradient(135deg,#1b5fa8,#5aa7e0)" role="img" aria-label="Clinician holding a phone with an AI heart graphic"></div><h4>AI power saves time and improves treatment plan quality</h4><div class="card-meta"><svg><use href="#cal"/></svg>Dec 10, 2020 &nbsp;|&nbsp; <svg><use href="#user"/></svg>Alex Reed</div><div class="card-link"><svg><use href="#doc"/></svg>DownLoad Now</div></article>
    <article class="card" style="left:227px"><div class="card-photo" style="background:linear-gradient(135deg,#9fb4c8,#e4e9ef 50%,#2d4f8a)" role="img" aria-label="Doctor reviewing a folder beside digital health screens"></div><h4>Leveraging Artificial Intelligence (AI) clinical decision support</h4><div class="card-meta"><svg><use href="#cal"/></svg>Dec 10, 2020 &nbsp;|&nbsp; <svg><use href="#user"/></svg>Alex Reed</div><div class="card-link"><svg><use href="#doc"/></svg>DownLoad Now</div></article>
    <article class="card" style="left:396px"><div class="card-photo" style="background:linear-gradient(135deg,#6fa7c9,#2f77a8 60%,#cfe2ee)" role="img" aria-label="Surgeons working in a bright operating room"></div><h4>Implementation and impact of AI decision support software</h4><div class="card-meta"><svg><use href="#cal"/></svg>Dec 10, 2020 &nbsp;|&nbsp; <svg><use href="#user"/></svg>Alex Reed</div><div class="card-link"><svg><use href="#doc"/></svg>DownLoad Now</div></article>
  </section>

  <section class="section partners" style="top:1280px">
    <h2 class="section-title">Our <em>Partners</em></h2>
    <div class="partner-grid">
      <div class="partner" style="color:#4e2a84">Northgate Health</div>
      <div class="partner" style="color:#b0123b">Riverbend Health</div>
      <div class="partner" style="color:#1d3c6e">Bayline Clinic</div>
      <div class="partner" style="color:#0a5fb4">Southmere Cancer Center</div>
      <div class="partner" style="color:#5b6670">Lakeshore Health</div>
      <div class="partner" style="color:#1f3d7a"><i style="background:#f28c28"></i>Harborview Cancer Institute</div>
      <div class="partner" style="color:#1e6e82">Eastfield General</div>
      <div class="partner" style="color:#1e3a6e">Kingsley Women's Hospital</div>
    </div>
  </section>

  <section class="section contact" style="top:1491px">
    <h2 class="section-title">Contact Us</h2>
    <div class="contact-item" style="left:40px"><div class="contact-icon"><svg><use href="#pin"/></svg></div><h5>California Address</h5><p>480 Harbor Loop, Suite<br>12 Millbrae, CA 94030</p></div>
    <div class="contact-item" style="left:174px"><div class="contact-icon"><svg><use href="#pin"/></svg></div><h5>Boston Address</h5><p>18 Elm Wharf Second Floor<br>Salem Bay, MA 01970</p></div>
    <div class="contact-item" style="left:307px"><div class="contact-icon"><svg><use href="#phone"/></svg></div><h5>Phone</h5><p>(555) 014-2290</p></div>
    <div class="contact-item" style="left:440px"><div class="contact-icon"><svg><use href="#mail"/></svg></div><h5>Email</h5><p>info@talvex-health.example<br>support@talvex-health.example</p></div>
  </section>

  <footer class="section footer" style="top:1654px">
    <div class="footer-brand">Talvex Health</div>
    <div class="social"><i></i><i></i><i></i><i></i></div>
    <div class="foot-col" style="left:212px">
      <h6>Our Office Address</h6>
      <div class="office-row"><svg><use href="#phone"/></svg><b>Phone</b>(555) 014-2290</div>
      <div class="office-row"><svg><use href="#mail"/></svg><b>Email</b>info@talvex-health.example</div>
      <div class="office-row"><svg><use href="#pin"/></svg><b>Location</b>480 Harbor Loop Suite 12<br>Millbrae, CA 94030</div>
    </div>
    <div class="foot-col" style="left:386px"><h6>Company</h6><a>Home</a><a>Solutions</a><a>Clinical Evidence</a><a>About</a><a>Contact Us</a></div>
    <div class="foot-col" style="left:493px"><h6>Information</h6><a>Terms &amp; Conditions</a><a>Privacy Policy</a><a>Disclaimer</a><a>Site Map</a><a>Customer Support</a></div>
    <div class="footer-rule"></div>
    <p class="copyright">Copyrights ©talvex-health 2020 | Allrights Reserved</p>
  </footer>
</main>

</body>
</html>
```